New Company Business Card design

Looking for a corporate looking business card utilising my new logo design - the logo i would like embossed as one option and flat as another - simplistic but stylish - less is more - we are an import export business launching into the market - i would like a couple of options as main background - Grey or Black

```html
<!DOCTYPE html>
<html lang="en">
<head>
<meta charset="utf-8">
<title>Meridian Trade Partners – Business Card</title>
<link rel="stylesheet" href="https://fonts.googleapis.com/css2?family=Open+Sans:wght@400;600;700&display=swap">
<style>
  :root {
    --stage: #2b2b2d;
    --card-white: #ffffff;
    --card-black: #231f20;
    --brand-blue: #2a73c0;
    --text-dark: #2a2a2a;
    --rule-grey: #9a9a9a;
    --muted-grey: #7a7a7a;
  }
  * { box-sizing: border-box; margin: 0; padding: 0; }
  html, body {
    width: 1200px; height: 900px; overflow: hidden;
    background: var(--stage);
    font-family: "Open Sans", Arial, sans-serif;
  }
  .stage { position: relative; width: 1200px; height: 900px; }
  .card {
    position: absolute; width: 560px; height: 320px;
    border-radius: 18px; overflow: hidden;
    box-shadow: 0 14px 30px rgba(0,0,0,.45);
  }
  .card--front { left: 90px; top: 110px; background: var(--card-white); }
  .card--back { left: 550px; top: 470px; background: var(--card-black); }
  .front-shapes { position: absolute; inset: 0; }

  .brand { position: absolute; left: 44px; top: 70px; }
  .brand__row { display: flex; align-items: center; gap: 12px; }
  .brand__dot { width: 30px; height: 30px; border-radius: 50%; background: var(--brand-blue); }
  .brand__name {
    color: var(--brand-blue); font-weight: 600; font-size: 30px;
    letter-spacing: .5px; line-height: 1;
  }
  .brand__sub {
    margin-top: 8px; color: var(--brand-blue); font-weight: 600;
    font-size: 13px; letter-spacing: 3px; text-transform: uppercase;
  }
  .brand__tagline {
    margin-top: 5px; color: var(--muted-grey); font-size: 8.5px;
    letter-spacing: 2.2px; text-transform: uppercase;
  }

  .person { position: absolute; right: 30px; top: 44px; text-align: right; }
  .person__name { color: var(--brand-blue); font-weight: 700; font-size: 17px; text-transform: uppercase; }
  .person__title { color: var(--text-dark); font-size: 12.5px; margin-bottom: 6px; }
  .person__address { color: var(--text-dark); font-size: 13px; line-height: 1.4; }

  .contacts { position: absolute; left: 30px; top: 218px; list-style: none; }
  .contacts li {
    display: flex; align-items: center; gap: 9px;
    color: var(--text-dark); font-size: 14px; line-height: 22px;
  }
  .contacts svg { width: 11px; height: 11px; fill: var(--brand-blue); flex: none; }

  .back-brand {
    position: absolute; inset: 0;
    display: flex; align-items: center; justify-content: center; gap: 16px;
  }
  .back-brand__dot { width: 46px; height: 46px; border-radius: 50%; background: var(--brand-blue); }
  .back-brand__name { color: var(--brand-blue); font-weight: 600; font-size: 44px; letter-spacing: .5px; }
</style>
</head>
<body>
<main class="stage">
  <section class="card card--front" aria-label="Business card front">
    <svg class="front-shapes" width="560" height="320" viewBox="0 0 560 320" aria-hidden="true">
      <line x1="0" y1="196" x2="470" y2="196" stroke="var(--rule-grey)" stroke-width="1"/>
      <path d="M560 205 H345 C330 205 326 213 322 226 L316 300 C314 312 311 320 304 320 H560 Z" fill="var(--card-black)"/>
      <line x1="0" y1="296" x2="318" y2="296" stroke="var(--brand-blue)" stroke-width="3"/>
    </svg>

    <div class="brand">
      <div class="brand__row">
        <span class="brand__dot"></span>
        <span class="brand__name">Meridian Trade</span>
      </div>
      <div class="brand__sub">Partners</div>
      <div class="brand__tagline">Worldwide supply for local markets</div>
    </div>

    <div class="person">
      <p class="person__name">Daniel Rowe</p>
      <p class="person__title">Founder/President</p>
      <p class="person__address">Po. box 418, Harbor Lane,<br>Westport, Zip Code - 00000</p>
    </div>

    <ul class="contacts">
      <li><svg viewBox="0 0 12 12"><path d="M3 0h6a1 1 0 0 1 1 1v10a1 1 0 0 1-1 1H3a1 1 0 0 1-1-1V1a1 1 0 0 1 1-1zm0 1.5v8h6v-8z"/></svg>(000) 555-01234</li>
      <li><svg viewBox="0 0 12 12"><path d="M0 2h12v8H0z M0 2l6 4.5L12 2" stroke="#fff" stroke-width=".8"/></svg>hello@meridiantrade.com</li>
      <li><svg viewBox="0 0 12 12"><circle cx="6" cy="6" r="5.5"/><path d="M0.5 6h11M6 .5v11" stroke="#fff" stroke-width=".8"/></svg>www.meridiantrade.com</li>
    </ul>
  </section>

  <section class="card card--back" aria-label="Business card back">
    <div class="back-brand">
      <span class="back-brand__dot"></span>
      <span class="back-brand__name">Meridian Trade</span>
    </div>
  </section>
</main>
</body>
</html>
```